Step and Repeat Backdrop for wedding reception photo booth

Would like to have a Step and Repeat Backdrop (8 foot high by 10 foot wide) that incorporates the wedding logo (attached) and the names Helen and Gavin. Background should be white, and wedding colors are burgundy and gold. Show me creativity :-) I have included some random samples.

```html
<!DOCTYPE html>
<html lang="en">
<head>
<meta charset="utf-8">
<title>Helen &amp; Gavin — Step and Repeat Backdrop</title>
<link href="https://fonts.googleapis.com/css2?family=Abril+Fatface&family=Playfair+Display:wght@500&display=swap" rel="stylesheet">
<style>
  :root {
    --page-bg: #e9e9e9;
    --backdrop-white: #ffffff;
    --gold-name: #cf9a2a;
    --gold-line: #c98f1e;
    --monogram-gold: #c4a46a;
  }
  html, body {
    margin: 0;
    padding: 0;
    width: 1200px;
    height: 2179px;
    overflow: hidden;
    background: var(--page-bg);
  }
  .backdrop {
    position: absolute;
    left: 60px;
    top: 657px;
    width: 1080px;
    height: 865px;
    background: var(--backdrop-white);
  }
  .monogram {
    position: absolute;
    width: 130px;
    margin-left: -65px;
    margin-top: -32px;
    text-align: center;
    font-family: "Playfair Display", Georgia, serif;
    font-weight: 500;
    font-size: 52px;
    line-height: 64px;
    letter-spacing: -2px;
    color: var(--monogram-gold);
    white-space: nowrap;
  }
  .couple-name {
    position: absolute;
    left: 0;
    width: 1080px;
    margin: 0;
    text-align: center;
    font-family: "Abril Fatface", Georgia, serif;
    font-weight: 400;
    font-size: 124px;
    line-height: 140px;
    letter-spacing: 2px;
    color: var(--gold-name);
    white-space: nowrap;
  }
  .name-first { top: 300px; }
  .name-second { top: 520px; }
  .ampersand-row {
    position: absolute;
    top: 448px;
    left: 250px;
    width: 580px;
    height: 80px;
  }
  .divider {
    position: absolute;
    top: 40px;
    height: 3px;
    background: linear-gradient(90deg, transparent, var(--gold-line) 12%, var(--gold-line) 88%, transparent);
  }
  .divider-left { left: 0; width: 240px; }
  .divider-right { right: 0; width: 240px; }
  .ampersand {
    position: absolute;
    left: 250px;
    top: 0;
    width: 80px;
    text-align: center;
    font-family: "Abril Fatface", Georgia, serif;
    font-size: 68px;
    line-height: 80px;
    color: var(--gold-name);
  }
</style>
</head>
<body>
  <main class="backdrop">
    <span class="monogram" style="left:113px;top:107px">H&amp;G</span>
    <span class="monogram" style="left:283px;top:107px">H&amp;G</span>
    <span class="monogram" style="left:453px;top:107px">H&amp;G</span>
    <span class="monogram" style="left:624px;top:107px">H&amp;G</span>
    <span class="monogram" style="left:794px;top:107px">H&amp;G</span>
    <span class="monogram" style="left:964px;top:107px">H&amp;G</span>

    <span class="monogram" style="left:113px;top:250px">H&amp;G</span>
    <span class="monogram" style="left:283px;top:250px">H&amp;G</span>
    <span class="monogram" style="left:453px;top:250px">H&amp;G</span>
    <span class="monogram" style="left:624px;top:250px">H&amp;G</span>
    <span class="monogram" style="left:794px;top:250px">H&amp;G</span>
    <span class="monogram" style="left:964px;top:250px">H&amp;G</span>

    <span class="monogram" style="left:103px;top:417px">H&amp;G</span>
    <span class="monogram" style="left:960px;top:417px">H&amp;G</span>

    <span class="monogram" style="left:113px;top:584px">H&amp;G</span>
    <span class="monogram" style="left:276px;top:584px">H&amp;G</span>
    <span class="monogram" style="left:804px;top:584px">H&amp;G</span>
    <span class="monogram" style="left:964px;top:584px">H&amp;G</span>

    <span class="monogram" style="left:113px;top:727px">H&amp;G</span>
    <span class="monogram" style="left:283px;top:727px">H&amp;G</span>
    <span class="monogram" style="left:453px;top:727px">H&amp;G</span>
    <span class="monogram" style="left:624px;top:727px">H&amp;G</span>
    <span class="monogram" style="left:794px;top:727px">H&amp;G</span>
    <span class="monogram" style="left:964px;top:727px">H&amp;G</span>

    <h1 class="couple-name name-first">Helen</h1>
    <div class="ampersand-row">
      <span class="divider divider-left"></span>
      <span class="ampersand">&amp;</span>
      <span class="divider divider-right"></span>
    </div>
    <h1 class="couple-name name-second">Gavin</h1>
  </main>
</body>
</html>
```